Family business needs stationery redesign with new logo

Family owned company, established in 1987 wanting a brand 'refresh'. We are an electrical, refrigeration and construction company based in the Barkly Region Northern Territory, Australia. We have a new logo we would like to use which is uploaded along with our current letterhead and email signature. We are also dropping the word 'contractors' so please do not include this on any designs. Please note also, the 'orange' color used in our logo and designs should be Northern Territory red ochre which is as follows:

RGB (Hex): #C75B12
PantoneĀ® 159 C
CMYK: 1 / 74 / 100 / 7

We are needing our stationery redesigned using our new logo. Please include letterheads, business cards, envelopes, and email signatures.

We currently use our business letterheads for quotations, invoices, letters, HR matters, and internal memos.

We also need a separate simplified letterhead for internal paperwork such as employee leave forms, meeting agendas, and meeting minutes etc.

Reason: Needing more submissions of full package designs. We are wanting all our stationery, including business cards, letterheads, email signatures, envelopes, etc to be cohesive. We also require ALL the information, as supplied on our template letterhead, to be included on the new letterhead designs. including electrical license no.etc Thank you, R&W

Reason: needing more time as work has got in the way of looking over designs. A lot of designs not meeting the brief/criteria.

Industry/Entity Type

Business

Colors
0355a3
f37122

Requirements
Must have
• The 'orange' color used in the designs should be Northern Territory red ochre which is as follows:
• RGB (Hex): #C75B12
• PantoneĀ® 159 C
• CMYK: 1 / 74 / 100 / 7
• ***MUST INCLUDE ALL INFORMATION THAT IS ON OUR CURRENT LETTERHEAD***
Should not have
• Please do not include the word 'contractors'

```html
<!DOCTYPE html>
<html lang="en">
<head>
<meta charset="utf-8">
<title>R&amp;W Stationery Suite</title>
<link href="https://fonts.googleapis.com/css2?family=Source+Sans+3:wght@400;600;700&display=swap" rel="stylesheet">
<style>
:root{
  --navy:#26336f;
  --ochre:#d2601a;
  --ink:#555a60;
  --paper:#ffffff;
  --stage:#2b2b2b;
}
*{margin:0;padding:0;box-sizing:border-box}
html,body{width:1200px;height:922px;overflow:hidden;background:var(--stage)}
body{position:relative;font-family:"Source Sans 3",sans-serif;color:var(--ink)}
.sheet{position:absolute;background:var(--paper);box-shadow:0 3px 8px rgba(0,0,0,.5);overflow:hidden}
.brand{position:absolute;display:flex;align-items:center;gap:6px;font-weight:700;color:var(--navy);line-height:1}
.brand .dot{border-radius:50%;background:var(--ochre);flex:none}
.brand.light{color:#fff}
.contact{position:absolute;line-height:1.3}
.contact p{display:flex;align-items:center;gap:4px;white-space:nowrap}
.contact svg{flex:none}
.name{font-weight:700;color:var(--navy)}
.bar{position:absolute;left:0;right:0;bottom:0;display:flex;color:#fff;font-size:8.5px}
.bar .services{flex:1;background:var(--navy);padding-left:32px;display:flex;align-items:center}
.bar .web{background:var(--ochre);display:flex;align-items:center;justify-content:center}
.sep{color:var(--ochre)}
.legal{position:absolute;left:0;right:0;text-align:center;font-size:8px;white-space:nowrap}
.legal .sep{margin:0 4px}
</style>
</head>
<body>
<svg width="0" height="0" style="position:absolute">
  <defs>
    <symbol id="i-phone" viewBox="0 0 10 10"><path d="M2 1l2 2-1 1.5c.8 1.4 1.5 2 2.5 2.5L7 6l2 2-1.5 1.5C5 9 1 5 .5 2.5z" fill="#d2601a"/></symbol>
    <symbol id="i-mobile" viewBox="0 0 10 10"><rect x="3" y=".5" width="4" height="9" rx=".8" fill="none" stroke="#d2601a" stroke-width="1.2"/></symbol>
    <symbol id="i-fax" viewBox="0 0 10 10"><rect x="1" y="3.5" width="8" height="5" rx="1" fill="#d2601a"/><rect x="3" y="1" width="4" height="3" fill="#d2601a"/></symbol>
    <symbol id="i-mail" viewBox="0 0 10 10"><rect x=".5" y="2" width="9" height="6" fill="#d2601a"/><path d="M.5 2l4.5 3.5L9.5 2" fill="none" stroke="#fff" stroke-width=".8"/></symbol>
    <symbol id="i-web" viewBox="0 0 10 10"><circle cx="5" cy="5" r="4.5" fill="#d2601a"/><path d="M.5 5h9M5 .5c-2 3-2 6 0 9M5 .5c2 3 2 6 0 9" stroke="#fff" stroke-width=".6" fill="none"/></symbol>
    <symbol id="i-pin" viewBox="0 0 10 10"><path d="M5 .5a3.2 3.2 0 0 1 3.2 3.2C8.2 6 5 9.5 5 9.5S1.8 6 1.8 3.7A3.2 3.2 0 0 1 5 .5z" fill="#d2601a"/><circle cx="5" cy="3.7" r="1.1" fill="#fff"/></symbol>
  </defs>
</svg>

<section class="sheet letterhead" style="left:20px;top:190px;width:549px;height:711px">
  <div class="brand" style="left:36px;top:38px;font-size:42px"><span>R&amp;W</span><span class="dot" style="width:12px;height:12px"></span></div>
  <div class="contact" style="left:379px;top:34px;font-size:8.5px">
    <p>PO Box 412, 58 Spinifex St</p>
    <p>Redgum Flats QZ 4729</p>
    <p style="margin-top:5px"><svg width="8" height="8"><use href="#i-phone"/></svg>08 8140 3271</p>
    <p><svg width="8" height="8"><use href="#i-fax"/></svg>08 8140 3299</p>
    <p><svg width="8" height="8"><use href="#i-mail"/></svg>dana@rwservices.com.au</p>
  </div>
  <p class="legal" style="top:672px">ABN 62 408 117 305<span class="sep">|</span>Refrigerant Trading Authorisation AU04718<span class="sep">|</span>State Electrical Contractors License 03917</p>
  <div class="bar" style="height:21px">
    <div class="services">Electrical <span class="sep">&nbsp;•&nbsp;</span> Refrigeration <span class="sep">&nbsp;•&nbsp;</span> Building Services</div>
    <div class="web" style="width:147px">www.rwservices.com.au</div>
  </div>
</section>

<section class="sheet email-signature" style="left:606px;top:22px;width:359px;height:140px">
  <div class="brand" style="left:18px;top:16px;font-size:22px"><span>R&amp;W</span><span class="dot" style="width:7px;height:7px"></span></div>
  <div class="contact" style="left:16px;top:58px;font-size:6.5px">
    <p class="name" style="font-size:10px">Dana Whitfield</p>
    <p>Corporate Services Manager, R&amp;W Services</p>
  </div>
  <div class="contact" style="left:16px;top:87px;font-size:6px">
    <p><svg width="6" height="6"><use href="#i-phone"/></svg>08 8140 3271</p>
    <p><svg width="6" height="6"><use href="#i-mobile"/></svg>0412 706 358</p>
    <p><svg width="6" height="6"><use href="#i-fax"/></svg>08 8140 3299</p>
    <p><svg width="6" height="6"><use href="#i-mail"/></svg>dana@rwservices.com.au</p>
    <p><svg width="6" height="6"><use href="#i-web"/></svg>www.rwservices.com.au</p>
  </div>
  <div class="contact" style="left:146px;top:112px;font-size:6px">
    <p><svg width="6" height="6"><use href="#i-pin"/></svg>PO Box 412, 58 Spinifex St</p>
    <p style="padding-left:10px">Redgum Flats QZ 4729</p>
  </div>
</section>

<section class="sheet card-front" style="left:606px;top:190px;width:226px;height:129px;border-radius:6px">
  <div class="brand" style="left:20px;top:50px;font-size:24px"><span>R&amp;W</span><span class="dot" style="width:7px;height:7px"></span></div>
  <div style="position:absolute;left:99px;top:22px;width:1px;height:86px;background:var(--navy)"></div>
  <div class="contact" style="left:108px;top:22px;font-size:5.5px;line-height:1.35">
    <p class="name" style="font-size:8.5px">Dana Whitfield</p>
    <p>Corporate Services Manager</p>
    <p>R&amp;W Services</p>
    <p style="margin-top:4px">PO Box 412, 58 Spinifex St</p>
    <p>Redgum Flats QZ 4729</p>
    <p style="margin-top:4px"><svg width="5" height="5"><use href="#i-phone"/></svg>08 8140 3271</p>
    <p><svg width="5" height="5"><use href="#i-mobile"/></svg>0412 706 358</p>
    <p><svg width="5" height="5"><use href="#i-fax"/></svg>08 8140 3299</p>
    <p><svg width="5" height="5"><use href="#i-mail"/></svg>dana@rwservices.com.au</p>
    <p><svg width="5" height="5"><use href="#i-web"/></svg>www.rwservices.com.au</p>
  </div>
</section>

<section class="sheet card-back" style="left:846px;top:190px;width:226px;height:129px;border-radius:6px;background:var(--navy)">
  <div class="brand light" style="left:0;right:0;justify-content:center;top:40px;font-size:32px"><span>R&amp;W</span><span class="dot" style="width:9px;height:9px"></span></div>
  <p style="position:absolute;left:0;right:0;top:110px;text-align:center;color:#fff;font-size:6px">Electrical <span class="sep">•</span> Refrigeration <span class="sep">•</span> Building Services</p>
</section>

<section class="sheet envelope-back" style="left:607px;top:366px;width:574px;height:250px">
  <svg style="position:absolute;left:0;top:0" width="574" height="74" viewBox="0 0 574 74">
    <path d="M0 0H574L566 50Q562 72 540 72H34Q12 72 8 50Z" fill="var(--navy)"/>
  </svg>
  <div class="brand light" style="left:0;right:0;justify-content:center;top:26px;font-size:22px"><span>R&amp;W</span><span class="dot" style="width:7px;height:7px"></span></div>
</section>

<section class="sheet envelope-front" style="left:606px;top:651px;width:574px;height:250px">
  <div class="brand" style="left:26px;top:26px;font-size:36px"><span>R&amp;W</span><span class="dot" style="width:10px;height:10px"></span></div>
  <div class="contact" style="left:25px;top:79px;font-size:8.5px;line-height:1.2">
    <p>PO Box 412, 58 Spinifex St</p>
    <p>Redgum Flats QZ 4729</p>
  </div>
  <div class="bar" style="height:21px">
    <div class="services">Electrical <span class="sep">&nbsp;•&nbsp;</span> Refrigeration <span class="sep">&nbsp;•&nbsp;</span> Building Services</div>
    <div class="web" style="width:141px">www.rwservices.com.au</div>
  </div>
</section>
</body>
</html>
```